Homepage for the brisk-find Web Application

At the end of this text, you will find a link to a website that is under construction for a webApp that I intend to launch soon. The contest goal is for you to make redesign the homepage in a nice, fresh, modern Style. Only design, no coding necessary. It needs to have a responsive version for small screens like smart phones. Attached is the text for it, and some images that you may use. You are welcome to find or create additional supporting images. You can use PixTrove.example or similar service to find new images as long as I can purchase the non-exclusive use rights for the images at similar prices. The contest is just for the home page. However, the winner, if I like the work and we can agree on a fair price, could be contracted on a one-on-one basis to do the rest of the site. You are welcome to suggest minor changes like font sizes and minor variations on the Header banner, but that banner is consistent with the user interface of the application therefore should not change too much. The information should flow somewhat continually without much use of side bars or things like that.
https://www.brisk-find.example
Sincerely,
Marco D. Ferral

```html
<!DOCTYPE html>
<html lang="en">
<head>
<meta charset="utf-8">
<title>Brisk Find — Home</title>
<link href="https://fonts.googleapis.com/css2?family=Raleway:ital,wght@0,300;0,400;0,600;0,700;0,800;1,300;1,400&family=Open+Sans:ital,wght@0,400;0,600;0,700;1,400&display=swap" rel="stylesheet">
<style>
:root{
  --orange:#ff7d4f;
  --teal:#4fd1d4;
  --blue:#1a79c4;
  --hero-blue:#2f7cc8;
  --deep-blue:#0a5aa8;
  --sky-blue:#14a6df;
  --pale-blue:#d6effb;
  --ink:#1d1d1d;
  --grey:#666;
  --light:#f2f2f2;
  --white:#fff;
}
*{box-sizing:border-box;margin:0;padding:0}
html,body{width:1200px;height:4046px;overflow:hidden}
body{font-family:"Open Sans",sans-serif;color:var(--ink);background:var(--white);position:relative}
section,header,footer{position:absolute;left:0;width:1200px}
.abs{position:absolute}
.center{text-align:center;left:0;width:1200px}
.btn{position:absolute;display:flex;align-items:center;justify-content:center;border-radius:30px;font-family:"Raleway",sans-serif;font-weight:700;color:var(--white);background:var(--orange);letter-spacing:1px}
.kicker{font-family:"Raleway",sans-serif;font-weight:700;font-size:11px;text-transform:uppercase}
.title{font-family:"Raleway",sans-serif;font-weight:600;font-size:31px}
.lead{font-size:12px;line-height:16px;color:var(--grey)}

.top-rule{top:0;height:6px;background:var(--orange)}
.site-header{top:6px;height:124px}
.brand{left:75px;top:34px;font-family:"Raleway",sans-serif;font-weight:600;font-size:48px;color:var(--teal);display:flex;align-items:center;gap:10px}
.brand-dot{width:14px;height:14px;border-radius:50%;background:var(--orange)}
.contact-line{left:741px;top:38px;font-size:11px;color:var(--grey)}
.contact-line b{color:var(--orange);font-weight:600}
.login{left:1062px;top:37px;font-size:12px;color:var(--blue);display:flex;gap:6px;align-items:center}
.main-nav{left:525px;top:76px;display:flex;gap:22px;font-size:12px;color:var(--blue)}
.trial-chip{left:1038px;top:69px;width:102px;height:30px;font-size:12px;letter-spacing:0}

.hero{top:130px;height:544px;background:var(--hero-blue);overflow:hidden}
.hero-photo{left:0;top:0;width:600px;height:544px;background:linear-gradient(120deg,#3a8ad4,#2b6fb8 60%,#5b6a7a)}
.hero-text{left:602px;top:140px;font-family:"Raleway",sans-serif}
.hero-text .intro{font-style:italic;font-weight:300;font-size:44px;color:var(--teal);line-height:44px}
.hero-text .big{font-weight:800;font-size:50px;color:var(--white);line-height:46px;letter-spacing:1px}
.hero-text .tail{font-weight:400;font-size:50px;color:var(--teal);line-height:52px}
.hero .btn{top:358px;height:51px;font-weight:400;font-size:20px;border-radius:6px;letter-spacing:0}
.btn-trial{left:609px;width:176px}
.btn-app{left:814px;width:207px;background:transparent;border:3px solid var(--white)}

.welcome{top:674px;height:383px}
.welcome-photo{left:132px;top:86px;width:314px;height:204px;background:linear-gradient(135deg,#8c939b,#3b4b5c)}
.welcome .kicker{left:484px;top:90px;color:var(--blue)}
.welcome .title{left:484px;top:106px;font-size:32px;font-weight:700}
.welcome .lead{left:484px;top:154px;width:586px;text-align:justify;line-height:15.5px}
.welcome .btn{left:484px;top:253px;width:113px;height:37px;font-size:10px}

.pricing{top:1057px;height:647px;background:var(--pale-blue)}
.pricing .kicker{top:66px;color:var(--blue)}
.pricing .title{top:84px}
.pricing .lead{top:127px}
.plan{position:absolute;top:214px;width:197px}
.plan-name{text-align:center;font-family:"Raleway",sans-serif;font-weight:700;font-size:13px}
.plan-card{margin-top:11px;background:var(--white);height:327px}
.plan-price{height:94px;background:var(--orange);color:var(--white);font-family:"Raleway",sans-serif;font-weight:800;font-size:52px;display:flex;align-items:center;justify-content:center}
.plan.featured .plan-price{background:var(--blue)}
.plan ul{list-style:none;padding:26px 0 0 33px;font-size:11.5px;color:var(--grey)}
.plan li{height:31px;display:flex;align-items:flex-start;gap:10px}
.plan li svg{margin-top:2px}
.plan .btn{position:absolute;left:34px;top:273px;width:116px;height:37px;background:var(--blue);font-size:11px;letter-spacing:0}

.blog{top:1704px;height:657px}
.blog .kicker{top:70px;color:var(--blue)}
.blog .title{top:88px}
.blog .lead{top:126px}
.post{position:absolute;top:203px;width:284px}
.post-photo{height:188px}
.post-meta{margin:20px 0 0 17px;font-size:9.5px;font-weight:600}
.post-title{margin:14px 0 0 17px;font-family:"Raleway",sans-serif;font-weight:700;font-size:17px;line-height:19px;color:var(--orange)}
.post-text{margin:14px 0 0 17px;width:250px;font-size:10px;line-height:14px;color:#888}
.post .btn{position:relative;margin:16px 0 0 14px;width:115px;height:26px;font-size:9px}

.download{top:2361px;height:413px;background:linear-gradient(100deg,var(--deep-blue),var(--sky-blue));color:var(--white)}
.download .title{top:92px;color:var(--white)}
.download .lead{top:164px;left:230px;width:740px;text-align:center;color:var(--white)}
.store{position:absolute;top:254px;height:44px;border:2px solid var(--white);border-radius:8px;display:flex;align-items:center;justify-content:center;gap:8px;font-family:"Raleway",sans-serif;font-weight:700;font-size:12px}
.store i{width:14px;height:14px;background:var(--white);border-radius:3px}

.reviews{top:2774px;height:512px}
.reviews .title{top:72px}
.reviews .lead{top:120px}
.avatar{left:555px;top:177px;width:70px;height:70px;border-radius:50%;background:linear-gradient(160deg,#3d4a63,#1c2333)}
.reviewer{top:246px;font-family:"Raleway",sans-serif;font-weight:700;font-size:25px;color:var(--blue)}
.stars{top:280px;color:var(--orange);font-size:13px;letter-spacing:2px}
.quote{top:323px;left:300px;width:600px;text-align:center;font-style:italic;font-size:12px;line-height:16px;color:#444}
.dots{top:427px;left:546px;display:flex;gap:9px}
.dots span{width:6px;height:6px;border-radius:50%;background:#ccc}
.dots span:first-child{background:#888}

.contact{top:3286px;height:517px;background:var(--light)}
.contact .title{top:84px}
.contact .lead{top:130px}
.field{position:absolute;background:var(--white);border:1px solid #ddd;font-size:12px;color:#888;padding:0 17px;display:flex;align-items:center}
.field.area{align-items:flex-start;padding-top:16px}
.contact .btn{left:532px;top:418px;width:145px;height:37px;font-size:11px;letter-spacing:0}

.site-footer{top:3803px;height:243px;background:linear-gradient(100deg,var(--deep-blue),var(--sky-blue))}
.social{position:absolute;top:60px;width:62px;height:62px;border:2px solid rgba(255,255,255,.55);border-radius:50%;display:flex;align-items:center;justify-content:center}
.social i{width:14px;height:14px;background:var(--orange);border-radius:2px}
.copyright{top:170px;font-size:12px;color:var(--white)}
</style>
</head>
<body>

<div class="top-rule abs" style="left:0;width:1200px"></div>

<header class="site-header">
  <div class="brand abs">Brisk Find <span class="brand-dot"></span></div>
  <div class="contact-line abs"><b>Call Us</b> 555.010.742 &nbsp;&nbsp;&nbsp;<b>Email :</b> info@briskfind.example</div>
  <div class="login abs">Login
    <svg width="18" height="18" viewBox="0 0 18 18" fill="none" stroke="#ff7d4f" stroke-width="1.4"><circle cx="9" cy="6" r="4"/><path d="M2 17c0-4 3-6 7-6s7 2 7 6"/></svg>
  </div>
  <nav class="main-nav abs">
    <span>Home</span><span>About us</span><span>Pricing</span><span>Blog</span><span>FAQS</span><span>Support</span><span>Reviews</span><span>Contact us</span>
  </nav>
  <div class="btn trial-chip">Free - Trail</div>
</header>

<section class="hero">
  <div class="hero-photo abs" role="img" aria-label="Hands holding a smartphone showing a document-tracking app"></div>
  <div class="hero-text abs">
    <div class="intro">Keeping track of all your</div>
    <div class="big">PAPER DOCUMENTS</div>
    <div class="big">&amp; OTHER BELONGINGS</div>
    <div class="tail">has never been easier!</div>
  </div>
  <div class="btn btn-trial">Free Trial</div>
  <div class="btn btn-app">Download App</div>
</section>

<section class="welcome">
  <div class="welcome-photo abs" role="img" aria-label="Person browsing folders in a filing cabinet drawer"></div>
  <div class="kicker abs">Find any document or item instantly!</div>
  <h1 class="title abs">Welcome to Brisk Find</h1>
  <p class="lead abs">Brisk-Find is a system that allows you to quickly search for the location of every item that you store or file. It is an essential tool for keeping track of paper documents or any other kind of physical item. You'll have the ability to quickly find any item you're searching for, even years after you've stored it. More importantly, using Brisk-Find helps you save considerable space without losing speedy accessibility to your treasured items.</p>
  <div class="btn">READ MORE</div>
</section>

<section class="pricing">
  <div class="kicker abs center">Get started now</div>
  <h2 class="title abs center">Our Pricing Plans</h2>
  <p class="lead abs center">Lorem ipsum dolor sit amet, consectetur adipiscing elit. Quid autem<br>habent admirationis, cum prope accesseris</p>

  <div class="plan" style="left:171px">
    <div class="plan-name">STANDARD</div>
    <div class="plan-card"><div class="plan-price">$125</div>
      <ul>
        <li><svg width="10" height="9"><path d="M1 5l3 3 5-7" stroke="#ff7d4f" stroke-width="1.8" fill="none"/></svg>Dolor sit amet</li>
        <li><svg width="10" height="9"><path d="M1 5l3 3 5-7" stroke="#ff7d4f" stroke-width="1.8" fill="none"/></svg>Nam quibus rebus</li>
        <li><svg width="10" height="9"><path d="M1 5l3 3 5-7" stroke="#ff7d4f" stroke-width="1.8" fill="none"/></svg>Collatio igitur ista</li>
        <li><svg width="10" height="9"><path d="M1 5l3 3 5-7" stroke="#ff7d4f" stroke-width="1.8" fill="none"/></svg>Hoc non est</li>
      </ul>
      <div class="btn" style="top:299px">Purchase</div>
    </div>
  </div>
  <div class="plan" style="left:391px">
    <div class="plan-name">BRONZE</div>
    <div class="plan-card"><div class="plan-price">$256</div>
      <ul>
        <li><svg width="10" height="9"><path d="M1 5l3 3 5-7" stroke="#ff7d4f" stroke-width="1.8" fill="none"/></svg>Dolor sit amet</li>
        <li><svg width="10" height="9"><path d="M1 5l3 3 5-7" stroke="#ff7d4f" stroke-width="1.8" fill="none"/></svg>Nam quibus rebus</li>
        <li><svg width="10" height="9"><path d="M1 5l3 3 5-7" stroke="#ff7d4f" stroke-width="1.8" fill="none"/></svg>Collatio igitur ista</li>
        <li><svg width="10" height="9"><path d="M1 5l3 3 5-7" stroke="#ff7d4f" stroke-width="1.8" fill="none"/></svg>Hoc non est</li>
      </ul>
      <div class="btn" style="top:299px">Purchase</div>
    </div>
  </div>
  <div class="plan featured" style="left:611px">
    <div class="plan-name">GOLD</div>
    <div class="plan-card"><div class="plan-price">$645</div>
      <ul>
        <li><svg width="10" height="9"><path d="M1 5l3 3 5-7" stroke="#ff7d4f" stroke-width="1.8" fill="none"/></svg>Dolor sit amet</li>
        <li><svg width="10" height="9"><path d="M1 5l3 3 5-7" stroke="#ff7d4f" stroke-width="1.8" fill="none"/></svg>Nam quibus rebus</li>
        <li><svg width="10" height="9"><path d="M1 5l3 3 5-7" stroke="#ff7d4f" stroke-width="1.8" fill="none"/></svg>Collatio igitur ista</li>
        <li><svg width="10" height="9"><path d="M1 5l3 3 5-7" stroke="#ff7d4f" stroke-width="1.8" fill="none"/></svg>Hoc non est</li>
      </ul>
      <div class="btn" style="top:299px">Purchase</div>
    </div>
  </div>
  <div class="plan" style="left:829px">
    <div class="plan-name">COMPLETE</div>
    <div class="plan-card"><div class="plan-price">$895</div>
      <ul>
        <li><svg width="10" height="9"><path d="M1 5l3 3 5-7" stroke="#ff7d4f" stroke-width="1.8" fill="none"/></svg>Dolor sit amet</li>
        <li><svg width="10" height="9"><path d="M1 5l3 3 5-7" stroke="#ff7d4f" stroke-width="1.8" fill="none"/></svg>Nam quibus rebus</li>
        <li><svg width="10" height="9"><path d="M1 5l3 3 5-7" stroke="#ff7d4f" stroke-width="1.8" fill="none"/></svg>Collatio igitur ista</li>
        <li><svg width="10" height="9"><path d="M1 5l3 3 5-7" stroke="#ff7d4f" stroke-width="1.8" fill="none"/></svg>Hoc non est</li>
      </ul>
      <div class="btn" style="top:299px">Purchase</div>
    </div>
  </div>
</section>

<section class="blog">
  <div class="kicker abs center">Ostrud an est</div>
  <h2 class="title abs center">Lates Blog</h2>
  <p class="lead abs center">Lorem ipsum dolor sit amet, cu per porro dolore nostro, partem cu per porro<br>integre corpora per ea, tation ornatus mel ad</p>

  <article class="post" style="left:140px">
    <div class="post-photo" role="img" aria-label="Hand holding a smartphone beside a coffee cup and laptop" style="background:linear-gradient(135deg,#e9e6e2,#b9b3ad)"></div>
    <div class="post-meta">By Admin | 4 January 2021</div>
    <h3 class="post-title">Lorem ipsum dolor sit amet cu per porro dolore nostro</h3>
    <p class="post-text">Lorem ipsum dolor sit amet, cu per porro dolore nostro, partem integre corpora per ea, tation ornatus mel ad Brute voluptatibus an</p>
    <div class="btn">READ MORE</div>
  </article>
  <article class="post" style="left:446px">
    <div class="post-photo" role="img" aria-label="Two colleagues looking at a computer screen" style="background:linear-gradient(135deg,#3b4656,#1f2630)"></div>
    <div class="post-meta">By Admin | 4 January 2021</div>
    <h3 class="post-title">Sum dolor sit amet cu per porro dolore nostro</h3>
    <p class="post-text">Lorem ipsum dolor sit amet, cu per porro dolore nostro, partem integre corpora per ea, tation ornatus mel ad Brute voluptatibus an</p>
    <div class="btn">READ MORE</div>
  </article>
  <article class="post" style="left:754px">
    <div class="post-photo" role="img" aria-label="Woman smiling at her phone by a window" style="background:linear-gradient(135deg,#6b5a43,#c69a3a)"></div>
    <div class="post-meta">By Admin | 4 January 2021</div>
    <h3 class="post-title">Porro dolore nostro Lorem ipsum dolor sit ametcu per</h3>
    <p class="post-text">Lorem ipsum dolor sit amet, cu per porro dolore nostro, partem integre corpora per ea, tation ornatus mel ad Brute voluptatibus an</p>
    <div class="btn" style="margin-top:12px">READ MORE</div>
  </article>
</section>

<section class="download">
  <h2 class="title abs center">Download App</h2>
  <p class="lead abs">Lorem ipsum dolor sit amet, consectetur adipiscing elit. Quid autem habent admirationis cum prope accesseris An hoc usque c um propequaque, aliter in vita cum prope accesseris Lorem ipsum dolor sit amet, consectetur adipiscing elit. Quid autem habent um propequaque, aliter in vita cum prope accesseris Lorem ipsum dolor sit amet, consectetur adipiscing elit. Quid autem habent admirationis cum prope accesseris? An hoc usque cum propequaque, aliter in vita cum prope accesseris</p>
  <div class="store" style="left:339px;width:145px"><i></i>APP SHOP</div>
  <div class="store" style="left:499px;width:159px"><i></i>PLAY MARKET</div>
  <div class="store" style="left:674px;width:187px"><i></i>DESKTOP MARKET</div>
</section>

<section class="reviews">
  <h2 class="title abs center">Customers Reviews</h2>
  <p class="lead abs center" style="color:#444">Constructio interrete. Quia nec honesto quic quam honestius nec turpi turpius.<br>Tria genera bonorum; Quid iudicant sensus?</p>
  <svg class="abs" style="left:134px;top:226px" width="32" height="58"><path d="M28 2L4 29l24 27" stroke="#666" stroke-width="2" fill="none"/></svg>
  <svg class="abs" style="left:1016px;top:226px" width="32" height="58"><path d="M4 2l24 27L4 56" stroke="#666" stroke-width="2" fill="none"/></svg>
  <div class="avatar abs" role="img" aria-label="Customer portrait"></div>
  <div class="reviewer abs center">Jon Halver</div>
  <div class="stars abs center">★★★★★</div>
  <p class="quote abs">Constructio interrete. Quia nec honesto quic quam honestius nec turpi turpius. Tria genera bonorum; Quid iudicant sensus? Quae qui non vident, nihil umquam magnum ac cognitione dignum amaverunt. Dicet pro me ipsa virtus nec untur. Paulum, cum regem</p>
  <div class="dots abs"><span></span><span></span><span></span><span></span><span></span><span></span><span></span></div>
</section>

<section class="contact">
  <h2 class="title abs center">Get in Touch</h2>
  <p class="lead abs center">Lorem ipsum dolor sit amet, consectetur adipiscing elit. Quid autem habent admirationis,<br>Non igitur de improbo, sed de callido improbo quaerimus, qualis</p>
  <div class="field" style="left:258px;top:215px;width:336px;height:36px">Name*</div>
  <div class="field" style="left:258px;top:270px;width:336px;height:38px">Email*</div>
  <div class="field" style="left:258px;top:325px;width:336px;height:38px">Phone*</div>
  <div class="field area" style="left:617px;top:215px;width:335px;height:148px">Comment*</div>
  <div class="btn">SEND MESSAGE</div>
</section>

<footer class="site-footer">
  <div class="social" style="left:390px"><i></i></div>
  <div class="social" style="left:462px"><i></i></div>
  <div class="social" style="left:534px"><i></i></div>
  <div class="social" style="left:607px"><i></i></div>
  <div class="social" style="left:679px"><i></i></div>
  <div class="social" style="left:751px">
    <svg width="18" height="13" viewBox="0 0 18 13"><rect x="0" y="0" width="18" height="13" rx="2" fill="#ff7d4f"/><path d="M1 1l8 6 8-6" stroke="#fff" stroke-width="1.3" fill="none"/></svg>
  </div>
  <div class="copyright abs center">© 2021 Company Name All Right Reserved</div>
</footer>

</body>
</html>
```